Full 10+ Page Online Learning eBook Design - NOT just the cover :)

We currently have an eBook within the online learning space which is geared towards a consumer audience (hobbyists, interests), but we have a new 2.0 version which is geared towards professionals (certifications, training, continuing ed, career-oriented). We need a new design and need the words/copy put into the eBook, but want to keep the look and feel of the original (open to variations in design). File is attached, along with various logo options.

Target Market(s)

Professionals

Industry/Entity Type

Learning

Font styles to use
Sans Serif

Colors
33a6d7
acd036
919191

Requirements
Must have
• Must follow a very similar look a feel of the original file. We use a lot of fonts like Raleway, Gotham, Helvetica Neue, Gil Sans, DIN - anything modern looking. We also use a lot of grayish hexagons in our corporate design. Feel free to check out brightlanternhub.example to get a better sense.
Nice to have
• Include some professionally oriented icons / photos
Should not have
• No cartoonish graphics or imagery

```html
<!DOCTYPE html>
<html lang="en">
<head>
<meta charset="utf-8">
<title>Choosing the Right Platform</title>
<link href="https://fonts.googleapis.com/css2?family=Lato:wght@400&family=Cabin:wght@400&display=swap" rel="stylesheet">
<style>
  :root {
    --brand-blue: #33a6d7;
    --brand-green: #acd036;
    --brand-grey: #919191;
    --ink: #2b2b2b;
    --paper: #ffffff;
    --night-sky: #0f2f5a;
    --horizon: #3fb6e0;
    --water: #1f8fc4;
    --deep: #0a1c2e;
  }
  * { margin: 0; padding: 0; box-sizing: border-box; }
  html, body { width: 852px; height: 1200px; overflow: hidden; background: var(--paper); }
  .page {
    position: relative;
    width: 852px;
    height: 1200px;
    background: var(--paper);
    font-family: "Lato", "Helvetica Neue", sans-serif;
    color: var(--ink);
  }
  .band {
    position: absolute;
    left: 0;
    width: 852px;
    height: 14px;
    background: var(--brand-grey);
  }
  .band--top { top: 0; }
  .band--bottom { bottom: 0; }
  .hex-texture {
    position: absolute;
    right: 0;
    top: 470px;
    width: 360px;
    height: 218px;
    background: radial-gradient(ellipse at 80% 60%, rgba(172, 208, 54, 0.12), rgba(255, 255, 255, 0) 70%);
  }
  .content {
    position: absolute;
    left: 8px;
    top: 40px;
    width: 830px;
  }
  .section-title {
    font-family: "Cabin", "Gill Sans", sans-serif;
    font-weight: 400;
    font-size: 19px;
    letter-spacing: 0.2px;
    color: #1d1d1d;
    padding-bottom: 6px;
    width: 622px;
    border-bottom: 2px solid var(--brand-blue);
    margin-bottom: 10px;
  }
  .copy {
    font-size: 16.6px;
    line-height: 20.4px;
    margin-bottom: 20.4px;
  }
  .feature-list {
    list-style: none;
    font-size: 16.6px;
    line-height: 20.4px;
    margin-bottom: 20.4px;
  }
  .feature-list li::before { content: "\2022\00a0"; }
  .hero-photo {
    position: absolute;
    left: 0;
    top: 688px;
    width: 852px;
    height: 498px;
    border-top: 1px solid #d8e3ea;
    background:
      linear-gradient(180deg, var(--night-sky) 0%, #1c5e97 22%, var(--horizon) 38%, #0d2a3f 42%, var(--water) 52%, #145f8c 70%, var(--deep) 100%);
  }
</style>
</head>
<body>
  <main class="page">
    <div class="band band--top"></div>

    <section class="content">
      <h1 class="section-title">CHOOSING THE RIGHT PLATFORM</h1>

      <p class="copy">Building a learning business has traditionally required multiple programs:</p>

      <ul class="feature-list">
        <li>An authoring system;</li>
        <li>A learning object repository;</li>
        <li>User and customer management;</li>
        <li>Ecommerce operations;</li>
        <li>Licensing management;</li>
        <li>White labeling and affiliate management;</li>
        <li>Front-end and back-end reporting; and</li>
        <li>Middleware to hook these applications together.</li>
      </ul>

      <p class="copy">A best-of-breed solution knits those functions together into a single seamless platform to<br>help you run your learning business far more efficiently.</p>

      <p class="copy">Bright Lantern Hub specializes in powering the business of learning. Our SaaS platform<br>delivers the features and functions required for your entire ecosystem, from creation and<br>delivery of content through customer management and monetization.</p>

      <p class="copy">Because we know that building or transforming a business requires more than just technology,<br>Bright Lantern Hub also provides a highly-experienced professional services team to coach<br>customers through set-up of their learning programs and to help them identify where to<br>bolster or fine-tune their efforts. By taking an accelerated approach, some of those clients<br>have launched successful online learning businesses in weeks.</p>

      <p class="copy">By partnering with Bright Lantern Hub, your organization will be able to achieve more<br>engaging learning experiences, superior products that encourage better learner outcomes,<br>and more effective performance, distribution and management of your learning business.</p>
    </section>

    <div class="hex-texture" role="img" aria-label="Faint grey and green hexagon pattern"></div>

    <div class="hero-photo" role="img" aria-label="Photograph of a wooden pier stretching into blue water at dusk, lit by a lamp post"></div>

    <div class="band band--bottom"></div>
  </main>
</body>
</html>
```